Business Card Design for Mortgage Broking Business

We need to redesign the business card. Mortgage broking business, doing home loan and commercial loans, existing logo, also QLBT member logo. design style needs to be simple, professional, elegant.

once final, need to setup for a team of different names and contact details.

Industry/Entity Type

Loan

Contact Information for Business Card

Name; Mobile; Email; Address; Tel; Fax; Australian Credit Licence: 618204

```html
<!DOCTYPE html>
<html lang="en">
<head>
<meta charset="utf-8">
<title>Keystone Home Finance – Business Card</title>
<link rel="stylesheet" href="https://fonts.googleapis.com/css2?family=Open+Sans:wght@400;600;700&display=swap">
<style>
  :root {
    --backdrop: #e6e6e6;
    --card: #ffffff;
    --navy: #243a8c;
    --blue: #2c8fd6;
    --green: #7cc242;
    --text: #2a3f8f;
    --muted: #4a5a96;
    --faint: #f1f1f1;
  }
  * { box-sizing: border-box; margin: 0; padding: 0; }
  html, body {
    width: 1200px; height: 852px; overflow: hidden;
    background: var(--backdrop);
    font-family: "Open Sans", Arial, sans-serif;
    color: var(--text);
  }
  .stage { position: relative; width: 1200px; height: 852px; }
  .card {
    position: absolute;
    width: 540px; height: 310px;
    background: var(--card);
    border-radius: 24px;
    box-shadow: 0 2px 6px rgba(0,0,0,0.12);
    overflow: hidden;
  }
  .card--front { left: 80px; top: 110px; }
  .card--back { left: 580px; top: 440px; }

  .pattern-area {
    position: absolute; right: 0; top: 0;
    width: 200px; height: 310px;
    background: linear-gradient(135deg, var(--faint) 0%, #fafafa 60%, #ffffff 100%);
  }

  .brand {
    position: absolute;
    display: flex; align-items: center;
    font-weight: 700; color: var(--navy);
    line-height: 1.1;
  }
  .brand__mark { background: var(--navy); flex: none; }
  .brand__name { display: block; }

  .card--front .brand { left: 80px; top: 108px; gap: 16px; font-size: 34px; }
  .card--front .brand__mark { width: 56px; height: 56px; }
  .card--front .brand__name { width: 240px; }

  .card--back .brand { left: 40px; top: 178px; gap: 10px; font-size: 19px; }
  .card--back .brand__mark { width: 32px; height: 32px; }
  .card--back .brand__name { width: 140px; }

  .person { position: absolute; left: 290px; top: 56px; }
  .person__name { font-size: 17px; font-weight: 700; color: var(--navy); }
  .person__role { font-size: 12px; color: var(--muted); }

  .contacts {
    position: absolute; left: 290px; top: 128px;
    list-style: none; font-size: 12.5px; color: var(--muted);
  }
  .contacts li { display: flex; align-items: center; gap: 8px; height: 21px; white-space: nowrap; }
  .contacts svg { width: 12px; height: 12px; fill: var(--navy); flex: none; }
  .contacts .fax { margin-left: 10px; }

  .member-badge {
    position: absolute; left: 308px; top: 232px;
    width: 96px; height: 34px;
    border: 2px solid var(--blue);
    border-radius: 3px;
    background: linear-gradient(90deg, #eef6ff, #f2f9ea);
  }
</style>
</head>
<body>
<main class="stage">
  <section class="card card--front" aria-label="Card front">
    <div class="pattern-area" role="img" aria-label="Faint decorative square pattern"></div>
    <div class="brand"><span class="brand__mark"></span><span class="brand__name">Keystone Home Finance</span></div>
  </section>

  <section class="card card--back" aria-label="Card back">
    <div class="brand"><span class="brand__mark"></span><span class="brand__name">Keystone Home Finance</span></div>

    <div class="person">
      <p class="person__name">Your Long Name</p>
      <p class="person__role">Managing Director</p>
    </div>

    <ul class="contacts">
      <li><svg viewBox="0 0 12 12"><path d="M6 0a4 4 0 0 0-4 4c0 3 4 8 4 8s4-5 4-8a4 4 0 0 0-4-4zm0 5.6A1.6 1.6 0 1 1 6 2.4a1.6 1.6 0 0 1 0 3.2z"/></svg>Your Commercial or office address</li>
      <li><svg viewBox="0 0 12 12"><path d="M2.5 0.5l2 2.5-1.2 1.4a7 7 0 0 0 4.3 4.3L9 7.5l2.5 2-1.3 2C5 11 1 7 0.5 1.8z"/></svg>00.00.00.0000
        <svg class="fax" viewBox="0 0 12 12"><path d="M3 0h6v3H3zM1 4h10v6H9v2H3v-2H1zm3 4v3h4V8z"/></svg>00.00.00.0000</li>
      <li><svg viewBox="0 0 12 12"><path d="M0 2h12v1L6 7 0 3zm0 2.5l6 4 6-4V10H0z"/></svg>yourname@yourwebsite.com</li>
      <li><svg viewBox="0 0 12 12"><path d="M6 0a6 6 0 1 0 0 12A6 6 0 0 0 6 0zm4.3 5H8.6a9 9 0 0 0-.8-3.4A4.6 4.6 0 0 1 10.3 5zM6 1.3c.6.9 1.1 2.2 1.2 3.7H4.8C4.9 3.5 5.4 2.2 6 1.3zM1.7 7h1.7a9 9 0 0 0 .8 3.4A4.6 4.6 0 0 1 1.7 7zm0-2a4.6 4.6 0 0 1 2.5-3.4A9 9 0 0 0 3.4 5zM6 10.7c-.6-.9-1.1-2.2-1.2-3.7h2.4c-.1 1.5-.6 2.8-1.2 3.7zm1.8-.3A9 9 0 0 0 8.6 7h1.7a4.6 4.6 0 0 1-2.5 3.4z"/></svg>www.yourwebsite.com</li>
    </ul>

    <div class="member-badge" role="img" aria-label="Industry membership badge"></div>
  </section>
</main>
</body>
</html>
```